Whitcombe Business Card Design

The name of the business is Dario Whitcombe, CPA LLC
The service that we offer is Accounting, Tax & Consulting Services. I need it to have the following items:
Dario Whitcombe, Principal
Phone Number
Email Address
Physical Address

I have attached the company logo, one in black and one in white. Please provide a design in black background and the other in white background. Please include "Accounting, Tax & Consulting Services". I want the business card to be clean and very professional.

```html
<!DOCTYPE html>
<html lang="en">
<head>
<meta charset="utf-8">
<title>Dario Whitcombe, CPA LLC – Business Card</title>
<link rel="stylesheet" href="https://fonts.googleapis.com/css2?family=Lato:wght@300;400;700&display=swap">
<style>
  :root {
    --backdrop: #1f1f20;
    --card-light: #ecedee;
    --card-dark: #3a3b3d;
    --accent-red: #9b1b1f;
    --ink-dark: #3c3c3e;
    --ink-muted: #55565a;
    --ink-light: #f2f2f2;
  }
  * { margin: 0; padding: 0; box-sizing: border-box; }
  html, body {
    width: 1200px; height: 1200px; overflow: hidden;
    background: var(--backdrop);
    font-family: "Lato", sans-serif;
  }
  .card {
    position: absolute; left: 228px;
    width: 744px; height: 429px;
  }
  .card--front { top: 149px; background: var(--card-light); }
  .card--back { top: 623px; background: var(--card-dark); }

  .holder {
    position: absolute; left: 0; width: 720px; top: 146px;
    text-align: center;
  }
  .holder__name {
    font-size: 23px; font-weight: 400; letter-spacing: 0.5px;
    color: var(--ink-dark);
  }
  .holder__first { color: var(--accent-red); }
  .holder__title {
    margin-top: 4px; font-size: 15px; font-weight: 400; color: var(--ink-muted);
  }
  .divider {
    position: absolute; left: 156px; top: 233px; width: 410px; height: 1.5px;
    background: var(--accent-red);
  }

  .contact {
    position: absolute; display: flex; align-items: center; gap: 16px;
  }
  .contact__icon {
    width: 32px; height: 32px; border-radius: 50%;
    background: var(--accent-red); flex: none;
    display: flex; align-items: center; justify-content: center;
  }
  .contact__text {
    font-size: 12px; line-height: 15px; font-weight: 400; color: var(--ink-muted);
  }
  .contact--phone { left: 73px; top: 292px; }
  .contact--email { left: 73px; top: 349px; }
  .contact--web { left: 474px; top: 291px; }
  .contact--address { left: 474px; top: 345px; }
  .contact--address .contact__text { margin-left: 6px; }

  .brand {
    position: absolute; left: 137px; top: 174px;
    display: flex; align-items: center; gap: 20px;
  }
  .brand__square {
    width: 56px; height: 56px; background: var(--ink-light); flex: none;
  }
  .brand__name {
    font-size: 30px; font-weight: 400; letter-spacing: 1px;
    color: var(--ink-light); line-height: 32px;
  }
  .brand__tagline {
    font-size: 20px; font-weight: 400; letter-spacing: 2.2px;
    color: var(--ink-light); line-height: 24px;
  }
  .service-band {
    position: absolute; left: 0; top: 0; width: 744px; height: 428px;
  }
  .service-band__text {
    position: absolute; left: 114px; width: 491px; top: 352px;
    text-align: center; font-size: 25px; font-weight: 400; color: var(--ink-dark);
  }
</style>
</head>
<body>

<section class="card card--front" aria-label="Business card, front">
  <div class="holder">
    <p class="holder__name"><span class="holder__first">DARIO</span> WHITCOMBE</p>
    <p class="holder__title">Principal</p>
  </div>
  <div class="divider"></div>

  <div class="contact contact--phone">
    <span class="contact__icon">
      <svg width="18" height="18" viewBox="0 0 24 24" fill="none" stroke="#fff" stroke-width="1.6" stroke-linejoin="round">
        <path d="M5 3h4l2 5-2.5 1.5a11 11 0 0 0 6 6L16 13l5 2v4a2 2 0 0 1-2 2A16 16 0 0 1 3 5a2 2 0 0 1 2-2z"/>
      </svg>
    </span>
    <p class="contact__text">+1 (555) 013 4820<br>+1 (555) 016 7391</p>
  </div>

  <div class="contact contact--email">
    <span class="contact__icon">
      <svg width="18" height="18" viewBox="0 0 24 24" fill="none" stroke="#fff" stroke-width="1.6" stroke-linejoin="round">
        <rect x="3" y="5" width="18" height="14" rx="1.5"/>
        <path d="M3 6l9 7 9-7"/>
      </svg>
    </span>
    <p class="contact__text">info@whitcombecpa.com</p>
  </div>

  <div class="contact contact--web">
    <span class="contact__icon">
      <svg width="20" height="20" viewBox="0 0 24 24" fill="none" stroke="#fff" stroke-width="1.4">
        <circle cx="12" cy="12" r="9"/>
        <ellipse cx="12" cy="12" rx="4" ry="9"/>
        <path d="M3 12h18M4.5 7.5h15M4.5 16.5h15"/>
      </svg>
    </span>
    <p class="contact__text">www.whitcombecpa.com<br>www.whitcombe-tax-advisors.com</p>
  </div>

  <div class="contact contact--address">
    <span class="contact__icon">
      <svg width="18" height="18" viewBox="0 0 24 24" fill="#fff">
        <path d="M12 2a7 7 0 0 0-7 7c0 5 7 13 7 13s7-8 7-13a7 7 0 0 0-7-7zm0 9.5A2.5 2.5 0 1 1 12 6.5a2.5 2.5 0 0 1 0 5z"/>
      </svg>
    </span>
    <p class="contact__text">PO Box 4120 Larkfield<br>Brookdale, AB T0X 2W2</p>
  </div>
</section>

<section class="card card--back" aria-label="Business card, back">
  <div class="brand">
    <span class="brand__square"></span>
    <div>
      <p class="brand__name">DARIO WHITCOMBE, CPA LLC</p>
      <p class="brand__tagline">CERTIFIED PUBLIC ACCOUNTANT</p>
    </div>
  </div>

  <svg class="service-band" viewBox="0 0 744 428" aria-hidden="true">
    <path fill="var(--card-light)" d="M0 376 H100 Q114 376 114 362 V357 Q114 345 126 345 H593 Q605 345 605 357 V362 Q605 376 619 376 H744 V428 H0 Z"/>
  </svg>
  <p class="service-band__text">Accounting, Tax &amp; Consulting Services</p>
</section>

</body>
</html>
```